Harborline Auto LLC

Car Dealer Customer Service
Address: 2874 Cresthaven Road, Shelbyville, TN 37162
web: www.harborlineautoxq.net
email: harborlineautoxq@mailnest.example
Phone: (931) 555-0148
Phone: (629) 555-0173

```html
<!DOCTYPE html>
<html lang="en">
<head>
<meta charset="utf-8">
<title>Harborline Auto LLC – Business Card</title>
<link rel="stylesheet" href="https://fonts.googleapis.com/css2?family=Poppins:wght@400;600;700&display=swap">
<style>
  :root {
    --backdrop: #2c2c2d;
    --card: #232325;
    --card-front: #1f1f21;
    --blue: #1f86c3;
    --blue-deep: #176a9c;
    --gold: #e8ae3a;
    --text: #e4e4e4;
    --white: #ffffff;
    --emboss: #141416;
  }
  * { margin: 0; padding: 0; box-sizing: border-box; }
  html, body { width: 1200px; height: 1138px; overflow: hidden; }
  body {
    background: var(--backdrop);
    font-family: "Poppins", sans-serif;
    position: relative;
  }
  .card {
    position: absolute;
    width: 620px;
    height: 374px;
    border-radius: 14px;
    overflow: hidden;
  }
  /* Front */
  .card-front {
    left: 274px; top: 186px;
    background: var(--card-front);
  }
  .front-mark {
    position: absolute;
    left: 0; right: 0; top: 88px;
    display: flex; flex-direction: column; align-items: center; gap: 18px;
  }
  .front-mark .mark-circle {
    width: 120px; height: 120px; border-radius: 50%;
    background: var(--emboss);
  }
  .front-mark .mark-name {
    font-weight: 700; font-size: 34px; letter-spacing: 1px;
    color: var(--emboss);
  }
  .front-web {
    position: absolute; left: 0; right: 0; top: 334px;
    display: flex; align-items: center; justify-content: center; gap: 22px;
    color: var(--text); font-size: 14.5px;
  }
  .front-web .rule { width: 54px; height: 2px; background: var(--gold); }

  /* Back */
  .card-back {
    left: 276px; top: 608px;
    background: var(--card);
  }
  .card-back .waves { position: absolute; left: 0; top: 0; }
  .phones {
    position: absolute; right: 30px; top: 22px;
    display: flex; flex-direction: column; gap: 6px;
    color: var(--white); font-weight: 700; font-size: 21px; letter-spacing: 1px;
  }
  .phones li { list-style: none; display: flex; align-items: center; gap: 10px; justify-content: flex-end; }
  .brand {
    position: absolute; left: 30px; top: 130px; width: 220px;
    display: flex; flex-direction: column; align-items: center; gap: 16px;
  }
  .brand .mark-circle {
    width: 132px; height: 132px; border-radius: 50%; background: var(--blue);
  }
  .brand .brand-name {
    font-weight: 700; font-size: 25px; color: var(--blue); white-space: nowrap;
  }
  .person {
    position: absolute; right: 30px; top: 178px; text-align: right;
  }
  .person .name { color: var(--blue); font-weight: 700; font-size: 23px; line-height: 1.2; }
  .person .role { color: var(--text); font-size: 15px; }
  .address {
    position: absolute; right: 30px; top: 248px; text-align: right;
    color: var(--text); font-size: 15px; line-height: 1.45; font-style: normal;
  }
  .contacts {
    position: absolute; right: 30px; top: 302px;
    color: var(--text); font-size: 15px; line-height: 1.45;
  }
  .contacts li { list-style: none; display: flex; align-items: center; justify-content: flex-end; gap: 10px; }
</style>
</head>
<body>

<section class="card card-front" aria-label="Card front">
  <div class="front-mark">
    <div class="mark-circle"></div>
    <div class="mark-name">HARBORLINE AUTO</div>
  </div>
  <div class="front-web">
    <span class="rule"></span>
    <span>www.harborlineautoxq.net</span>
    <span class="rule"></span>
  </div>
</section>

<section class="card card-back" aria-label="Card back">
  <svg class="waves" width="620" height="374" viewBox="0 0 620 374" aria-hidden="true">
    <defs>
      <linearGradient id="bandBlue" x1="0" y1="0" x2="1" y2="1">
        <stop offset="0" stop-color="var(--blue)"/>
        <stop offset="1" stop-color="var(--blue-deep)"/>
      </linearGradient>
    </defs>
    <path d="M0 0 H620 V116 C520 130 430 112 360 72 C280 26 150 8 0 26 Z" fill="url(#bandBlue)"/>
    <path d="M0 58 C150 28 290 38 380 84 C450 120 540 132 620 120 V132 C540 144 440 132 370 96 C280 50 150 44 0 68 Z" fill="var(--gold)"/>
  </svg>

  <ul class="phones">
    <li>931-555-0148
      <svg width="20" height="16" viewBox="0 0 20 16" aria-hidden="true"><path d="M2 6 C2 1 18 1 18 6 L15 7 L13 4 H7 L5 7 Z M5 8 H15 L17 15 H3 Z" fill="var(--white)"/><circle cx="10" cy="11.5" r="2" fill="var(--blue-deep)"/></svg>
    </li>
    <li>629-555-0173
      <svg width="20" height="16" viewBox="0 0 20 16" aria-hidden="true"><path d="M2 6 C2 1 18 1 18 6 L15 7 L13 4 H7 L5 7 Z M5 8 H15 L17 15 H3 Z" fill="var(--white)"/><circle cx="10" cy="11.5" r="2" fill="var(--blue-deep)"/></svg>
    </li>
  </ul>

  <div class="brand">
    <div class="mark-circle"></div>
    <div class="brand-name">HARBORLINE AUTO</div>
  </div>

  <div class="person">
    <div class="name">Darren Kessler</div>
    <div class="role">Managing Director</div>
  </div>

  <address class="address">2874 Cresthaven Road,<br>Shelbyville, TN 37162</address>

  <ul class="contacts">
    <li>www.harborlineautoxq.net
      <svg width="14" height="14" viewBox="0 0 14 14" aria-hidden="true"><circle cx="7" cy="7" r="6.5" fill="var(--gold)"/><path d="M0.5 7 H13.5 M7 0.5 V13.5 M7 0.5 C3 4 3 10 7 13.5 M7 0.5 C11 4 11 10 7 13.5" stroke="var(--card)" stroke-width="1" fill="none"/></svg>
    </li>
    <li>harborlineautoxq@mailnest.example
      <svg width="16" height="12" viewBox="0 0 16 12" aria-hidden="true"><rect width="16" height="12" rx="1" fill="var(--gold)"/><path d="M0.5 0.8 L8 7 L15.5 0.8" stroke="var(--card)" stroke-width="1.2" fill="none"/></svg>
    </li>
  </ul>
</section>

</body>
</html>
```